Brisk Fixwell business card

I need business card for my business, I think you have all my details.six months ago I design with you car wrap design. We would like to design both side of the card. On front of card we would like logo , Name and our contact details.
At the back we are looking to mentioned our services.
The name will be:
Faridoullan Mestor
Managing Director
Ph:07952338417
Email:info@brisk-fixwell.com
Web:www.brisk-fixwell.com
So we have our logo, you don’t need to change the logo.
Please see the attachment.
Thanks

Target Market(s)

Home improvement

Industry/Entity Type

Home Improvement

Contact Information for Business Card

Company name: Brisk Fixwell
Name: Faridoullan Mestor
Position: Director
Ph:07952338417
Web: www.brisk-fixwell.com
Add: 42 Corvale Road
Castlewick
CW3 9KD
SECOND PERSON
Nizamuddel mestor
Position: Handyman
Ph: 07812 564037
Email: info@brisk-fixwell.com
Add: 18 Brackwin Lane Road
Castlewick
TW6 2LB

```html
<!DOCTYPE html>
<html lang="en">
<head>
<meta charset="utf-8">
<title>Brisk Fixwell – Business Card</title>
<link href="https://fonts.googleapis.com/css2?family=Open+Sans:wght@400;700&display=swap" rel="stylesheet">
<style>
  :root {
    --navy: #27357f;
    --navy-deep: #223077;
    --red: #e4202a;
    --grey-text: #4a4a4a;
    --paper: #ffffff;
    --backdrop: #d9d9d9;
  }
  * { box-sizing: border-box; margin: 0; padding: 0; }
  html, body { width: 1200px; height: 801px; overflow: hidden; }
  body {
    background: var(--backdrop);
    font-family: "Open Sans", Arial, sans-serif;
    display: flex;
    align-items: center;
    justify-content: center;
    gap: 48px;
  }
  .card {
    width: 525px;
    height: 300px;
    border-radius: 2px;
    box-shadow: 0 10px 24px rgba(0,0,0,0.18);
    position: relative;
    overflow: hidden;
  }
  .card--front {
    background: var(--paper);
    border-bottom: 3px solid var(--navy);
  }
  .brand {
    position: absolute;
    left: 40px;
    top: 0;
    bottom: 0;
    width: 210px;
    display: flex;
    align-items: center;
    gap: 10px;
  }
  .brand__mark {
    width: 14px;
    height: 14px;
    background: var(--red);
    flex: none;
  }
  .brand__name {
    font-weight: 700;
    font-size: 25px;
    color: var(--navy);
    line-height: 1.1;
    white-space: nowrap;
  }
  .divider {
    position: absolute;
    left: 262px;
    top: 48px;
    bottom: 48px;
    width: 1px;
    background: var(--navy);
  }
  .contact {
    position: absolute;
    left: 282px;
    top: 58px;
    color: var(--grey-text);
    font-size: 13px;
    line-height: 1.5;
  }
  .contact__name {
    color: var(--navy);
    font-weight: 700;
    font-size: 17px;
    line-height: 1.3;
  }
  .contact__role { margin-bottom: 8px; }
  .contact__address { margin-bottom: 8px; }
  .contact__line {
    display: flex;
    align-items: center;
    gap: 7px;
  }
  .contact__icon { width: 10px; height: 10px; flex: none; }
  .card--back { background: var(--navy); }
  .card__pattern {
    position: absolute;
    inset: 0;
    background: linear-gradient(135deg, var(--navy-deep), var(--navy) 60%, #2d3d8c);
  }
  .back-brand {
    position: absolute;
    inset: 0;
    display: flex;
    align-items: center;
    justify-content: center;
    gap: 10px;
  }
  .back-brand .brand__mark { background: var(--paper); }
  .back-brand .brand__name { color: var(--paper); }
</style>
</head>
<body>
  <section class="card card--front">
    <div class="brand">
      <span class="brand__mark"></span>
      <span class="brand__name">Brisk Fixwell</span>
    </div>
    <div class="divider"></div>
    <div class="contact">
      <p class="contact__name">Faridoullan Mestor</p>
      <p class="contact__role">Director</p>
      <p class="contact__address">42 Corvale Road<br>Castlewick, CW3 9KD</p>
      <p class="contact__line">
        <svg class="contact__icon" viewBox="0 0 10 10"><path d="M2 0.5 L4 2.5 L3 3.8 Q4.5 6 6.2 7 L7.5 6 L9.5 8 L8 9.5 Q3.5 9 0.5 2 Z" fill="#e4202a"/></svg>
        07952338417
      </p>
      <p class="contact__line">
        <svg class="contact__icon" viewBox="0 0 10 10"><rect x="0.5" y="2" width="9" height="6.5" fill="#e4202a"/><path d="M0.5 2 L5 5.5 L9.5 2" stroke="#fff" stroke-width="0.9" fill="none"/></svg>
        info@brisk-fixwell.com
      </p>
      <p class="contact__line">
        <svg class="contact__icon" viewBox="0 0 10 10"><circle cx="5" cy="5" r="4.5" fill="#e4202a"/><path d="M0.5 5 H9.5 M5 0.5 Q2.5 5 5 9.5 M5 0.5 Q7.5 5 5 9.5" stroke="#fff" stroke-width="0.7" fill="none"/></svg>
        www.brisk-fixwell.com
      </p>
    </div>
  </section>

  <section class="card card--back">
    <div class="card__pattern" role="img" aria-label="Faint repeating brand emblem pattern on navy background"></div>
    <div class="back-brand">
      <span class="brand__mark"></span>
      <span class="brand__name">Brisk Fixwell</span>
    </div>
  </section>
</body>
</html>
```